Pyschiatry Experts need Marketing Campaign

Ad(s) developed for print advertising sharing our purpose and services, highlighting our medical care providers. Must be welcoming and inviting while displaying a high level of professionalism expected from a physician's office.

Target Market(s)

Local community

Industry/Entity Type

Psychiatry (Healthcare)

Requirements
Must have
• Staff pictures, 'Medication Management Experts', 'Prompt Appointments', 'ADD/ADHD, Bipolar Disorder, Depression, Anxiety, Schizophrenia, Grief Reaction and others' 'Virtual and In-Person Visits'
Nice to have
• Address: 412 E Marlowe Coeur d'Alene Phone (208)555-7193 website: BrightLoftCare.com Hours: Mon - Thur 7am - 6pm

```html
<!DOCTYPE html>
<html lang="en">
<head>
<meta charset="utf-8">
<title>BrightLoft Care – Mental Health Evaluations</title>
<link rel="stylesheet" href="https://fonts.googleapis.com/css2?family=Libre+Baskerville:wght@700&family=Poppins:wght@400;500;600;700&family=Oswald:wght@300;600&display=swap">
<style>
  :root {
    --paper: #f9f8f1;
    --backdrop: #d4d4d4;
    --forest: #0d3b26;
    --deep: #0b3822;
    --teal: #14a08a;
    --teal-dark: #0f9280;
    --lime: #a5e05a;
    --leaf: #7fcf3a;
    --ink: #1d2a24;
    --rule: #dcdcd2;
  }
  * { margin: 0; padding: 0; box-sizing: border-box; }
  html, body { width: 1200px; height: 908px; overflow: hidden; }
  body { background: var(--backdrop); font-family: "Poppins", sans-serif; color: var(--ink); }

  .ad { position: absolute; left: 0; top: 67px; width: 1200px; height: 774px; background: var(--paper); overflow: hidden; }
  .abs { position: absolute; }

  /* brand */
  .brand-mark { left: 150px; top: 52px; width: 60px; height: 60px; border-radius: 50%; background: var(--teal); }
  .brand-name { left: 50px; top: 128px; width: 260px; text-align: center; font-family: "Libre Baskerville", serif; font-weight: 700; font-size: 27px; line-height: 34px; color: var(--teal); letter-spacing: 1px; }
  .brand-divider { left: 333px; top: 54px; width: 2px; height: 135px; background: var(--teal); opacity: .6; }

  .headline { left: 358px; top: 42px; font-family: "Libre Baskerville", serif; font-weight: 700; font-size: 47px; line-height: 48px; color: var(--forest); }
  .headline .accent { color: var(--teal); }

  .intro { left: 65px; top: 217px; font-size: 25px; line-height: 29px; color: var(--forest); }
  .intro strong { font-weight: 700; }
  .dots { left: 67px; top: 286px; display: flex; gap: 4px; }
  .dots span { width: 6px; height: 6px; border-radius: 50%; background: var(--leaf); }
  .dots span:nth-child(3) { opacity: .5; }
  .dots span:nth-child(4) { opacity: .25; }

  .conditions { left: 62px; top: 300px; width: 222px; list-style: none; }
  .conditions li { display: flex; align-items: center; height: 41.5px; border-bottom: 1px solid var(--rule); font-size: 18px; color: var(--ink); }
  .conditions li:last-child { border-bottom: none; line-height: 20px; height: 52px; }
  .conditions .icon { width: 18px; height: 18px; border-radius: 50%; background: var(--leaf); margin-right: 23px; flex: none; }

  .portrait-main { left: 340px; top: 224px; width: 315px; height: 375px; border-radius: 150px 150px 30px 30px; background: linear-gradient(180deg, #f0c49c 0%, #f4a57c 55%, #2e2e2e 100%); }

  .visits-band { left: 0; top: 596px; width: 635px; height: 43px; background: var(--lime); border-radius: 0 6px 6px 0; }
  .visits-band span { position: absolute; left: 67px; top: 6px; font-weight: 700; font-size: 25px; letter-spacing: 3.9px; color: var(--forest); }

  .contact { left: 68px; top: 656px; font-size: 17px; line-height: 26px; color: var(--ink); }
  .contact svg { vertical-align: -2px; margin-right: 3px; }
  .contact .hours-label { color: var(--leaf); font-weight: 600; }
  .contact strong { color: var(--forest); font-weight: 700; }
  .contact-divider { left: 366px; top: 663px; width: 2px; height: 64px; background: var(--teal); }

  .prompt { left: 377px; top: 656px; font-family: "Libre Baskerville", serif; font-weight: 700; font-size: 33px; line-height: 41px; color: var(--forest); }
  .prompt .accent { color: var(--teal); }

  .web { left: 716px; top: 694px; font-weight: 600; font-size: 27px; letter-spacing: 4px; color: var(--ink); }
  .web .accent { color: var(--teal); }

  /* right panel */
  .panel { left: 753px; top: 37px; width: 644px; height: 644px; border-radius: 50%; background: var(--teal-dark); }
  .leaf-area { left: 1005px; top: 12px; width: 195px; height: 173px; background: linear-gradient(160deg, var(--lime) 0%, rgba(165,224,90,0) 80%); }
  .focus-ring { left: 925px; top: 213px; width: 300px; height: 300px; border-radius: 50%; border: 3px solid var(--lime); }
  .focus { left: 936px; top: 224px; width: 278px; height: 278px; border-radius: 50%; background: var(--deep); }
  .focus-text { right: 71px; top: 308px; text-align: right; font-family: "Oswald", sans-serif; font-size: 36px; line-height: 35px; text-transform: uppercase; }
  .focus-text .l1 { color: #fff; font-weight: 600; }
  .focus-text .l2 { color: #fff; font-weight: 300; }
  .focus-text .l3 { color: var(--lime); font-weight: 600; }

  .staff-photo { width: 118px; height: 118px; border-radius: 50%; border: 5px solid var(--lime); box-shadow: inset 0 0 0 4px var(--forest); background: radial-gradient(circle at 50% 40%, #8c8c8c, #3f4a52); }
  .staff-name { color: #fff; font-weight: 700; font-size: 17px; line-height: 18px; }
  .badge { display: inline-block; margin-top: 3px; padding: 1px 9px; border-radius: 8px; background: var(--lime); color: var(--forest); font-size: 8px; font-weight: 600; }
</style>
</head>
<body>
<main class="ad">
  <div class="abs panel"></div>
  <div class="abs leaf-area" role="img" aria-label="Decorative green leaves"></div>

  <div class="abs brand-mark"></div>
  <div class="abs brand-name">BRIGHTLOFT<br>CARE</div>
  <div class="abs brand-divider"></div>

  <h1 class="abs headline">Comprehensive<br>Mental Health<br><span class="accent">Evaluations</span></h1>

  <p class="abs intro">Experts in the entire<br><strong>Mental Health Spectrum</strong></p>
  <div class="abs dots"><span></span><span></span><span></span><span></span></div>

  <ul class="abs conditions">
    <li><span class="icon"></span>ADD/ADHD</li>
    <li><span class="icon"></span>Bipolar Disorder</li>
    <li><span class="icon"></span>Depression</li>
    <li><span class="icon"></span>Anxiety</li>
    <li><span class="icon"></span>Schizophrenia</li>
    <li><span class="icon"></span>Grief Reaction<br>&amp; others</li>
  </ul>

  <div class="abs portrait-main" role="img" aria-label="Photo of a calm woman meditating cross-legged with palms pressed together"></div>

  <div class="abs visits-band"><span>VIRTUAL AND IN-PERSON VISITS</span></div>

  <div class="abs contact">
    <div><svg width="14" height="14" viewBox="0 0 24 24"><path d="M6.6 10.8a15 15 0 0 0 6.6 6.6l2.2-2.2a1 1 0 0 1 1-.25 11.4 11.4 0 0 0 3.6.57 1 1 0 0 1 1 1V20a1 1 0 0 1-1 1A17 17 0 0 1 3 4a1 1 0 0 1 1-1h3.5a1 1 0 0 1 1 1c0 1.25.2 2.45.57 3.57a1 1 0 0 1-.25 1z" fill="var(--leaf)"/></svg>(208)555-7193</div>
    <div><svg width="12" height="15" viewBox="0 0 24 30"><path d="M12 0a10 10 0 0 0-10 10c0 7.5 10 20 10 20s10-12.5 10-20A10 10 0 0 0 12 0zm0 14a4 4 0 1 1 0-8 4 4 0 0 1 0 8z" fill="var(--leaf)"/></svg>412 E Marlowe Coeur d'Alene</div>
    <div><span class="hours-label">Hours:</span> Mon - Thur <span class="hours-label">|</span> <strong>7am - 6pm</strong></div>
  </div>
  <div class="abs contact-divider"></div>
  <p class="abs prompt">Prompt<br><span class="accent">Appointments</span></p>

  <p class="abs web">www.<span class="accent">brightloftcare</span>.com</p>

  <div class="abs focus-ring"></div>
  <div class="abs focus"></div>
  <p class="abs focus-text"><span class="l1">Medication</span><br><span class="l2">Management</span><br><span class="l3">Experts</span></p>

  <div class="abs staff-photo" style="left:809px;top:53px" role="img" aria-label="Headshot of Mark Delano"></div>
  <div class="abs" style="left:940px;top:98px"><div class="staff-name">Mark Delano</div><span class="badge">PMHNP-BC</span></div>

  <div class="abs staff-photo" style="left:697px;top:217px" role="img" aria-label="Headshot of Marla Whitcomb"></div>
  <div class="abs" style="left:831px;top:252px"><div class="staff-name">Marla<br>Whitcomb</div><span class="badge">PMHNP-BC</span></div>

  <div class="abs staff-photo" style="left:697px;top:410px" role="img" aria-label="Headshot of Glen Harrow"></div>
  <div class="abs" style="left:827px;top:450px"><div class="staff-name">Glen Harrow</div><span class="badge">PMHNP-BC</span></div>

  <div class="abs staff-photo" style="left:809px;top:557px" role="img" aria-label="Headshot of Ruth Ellery"></div>
  <div class="abs" style="left:943px;top:590px"><div class="staff-name">Ruth Ellery</div><span class="badge">PMHNP-BC, DNP</span></div>
</main>
</body>
</html>
```